Small Business Consulting Firm Needs Letterhead

We need a letterhead for our company "Brightpath Plus". Our company does outbound calling and mailing to business owner's companies who have taken high interest loans. These loans tend to put these businesses in a big financial bind short term, and we help them find better financial options. We would like the design to match our colors of our logo. Headers and footers would look nice, but we are open. We would want it to include our address, website, phone, and email info. Our address - 2000 E. Lamar Blvd. Suite 600Website - www.safeguardtoday.comEmail - info@safeguardtoday.comPhone - 855-726-1938
Industry/Entity Type
Financial Planning
Look and feel
Each slider illustrates characteristics of the customer's brand and the style your logo design should communicate.

```html
<!DOCTYPE html>
<html lang="en">
<head>
<meta charset="utf-8">
<title>Brightpath Plus Letterhead</title>
<link rel="stylesheet" href="https://fonts.googleapis.com/css2?family=Open+Sans:wght@400;600;700&display=swap">
<style>
  :root {
    --bg: #eeeeec;
    --paper: #ffffff;
    --ink: #1d1d1d;
    --ink-soft: #444444;
    --green: #5aad34;
    --blue: #0b4f8f;
    --rule: #111111;
  }
  * { box-sizing: border-box; margin: 0; padding: 0; }
  html, body { width: 1200px; height: 800px; overflow: hidden; }
  body {
    background: var(--bg);
    font-family: "Open Sans", sans-serif;
    color: var(--ink);
    position: relative;
  }
  .letterhead {
    position: absolute;
    left: 330px;
    top: 18px;
    width: 540px;
    height: 764px;
    background: var(--paper);
    box-shadow: 0 4px 18px rgba(0,0,0,0.12);
    overflow: hidden;
  }
  .band { position: absolute; left: 0; width: 100%; }
  .band--top-main { top: 0; height: 12px; background: var(--blue); }
  .band--top-accent { top: 12px; height: 4px; background: var(--green); }
  .band--bottom-accent { bottom: 12px; height: 4px; background: var(--green); }
  .band--bottom-main { bottom: 0; height: 12px; background: var(--blue); }
  .brand {
    position: absolute;
    top: 104px;
    left: 0;
    width: 100%;
    display: flex;
    justify-content: center;
    align-items: center;
    gap: 10px;
  }
  .brand__square {
    width: 14px;
    height: 14px;
    background: var(--green);
  }
  .brand__name {
    font-size: 19px;
    font-weight: 400;
    letter-spacing: 2px;
    text-transform: uppercase;
    color: var(--ink-soft);
  }
  .header-rule {
    position: absolute;
    top: 150px;
    left: 50px;
    right: 50px;
    height: 2px;
    background: var(--rule);
  }
  .contact {
    position: absolute;
    top: 157px;
    left: 0;
    width: 100%;
    display: flex;
    justify-content: center;
    gap: 12px;
    font-size: 8px;
    color: var(--ink);
  }
  .contact__label { color: var(--green); font-weight: 700; margin-right: 2px; }
  .letter {
    position: absolute;
    top: 282px;
    left: 60px;
    right: 55px;
    font-size: 9px;
    line-height: 15px;
    color: var(--ink);
  }
  .letter__date { text-align: right; margin-bottom: 4px; }
  .letter__para { margin-bottom: 14px; }
  .signature {
    margin-top: 20px;
    width: 90px;
    height: 22px;
    background: #ececec;
  }
  .signoff__name { font-weight: 700; margin-top: 4px; line-height: 11px; }
  .signoff__role { line-height: 11px; }
  .footer-web {
    position: absolute;
    bottom: 52px;
    left: 0;
    width: 100%;
    text-align: center;
    padding-right: 120px;
    font-size: 8.5px;
    font-weight: 700;
    letter-spacing: 2.5px;
    color: var(--ink);
  }
  .footer-web__prefix { color: var(--green); }
</style>
</head>
<body>
  <main class="letterhead">
    <div class="band band--top-main"></div>
    <div class="band band--top-accent"></div>

    <header>
      <div class="brand">
        <span class="brand__square"></span>
        <span class="brand__name">Brightpath Plus</span>
      </div>
      <div class="header-rule"></div>
      <div class="contact">
        <span><span class="contact__label">A:</span>4170 W. Corwin Ave. Suite 310</span>
        <span><span class="contact__label">E:</span>info@brightpathplus.com</span>
        <span><span class="contact__label">P:</span>855-726-1938</span>
      </div>
    </header>

    <section class="letter">
      <p class="letter__date">Date, 10 September, 2019</p>
      <p class="letter__para">This is a sample letter that has been placed to demonstrate typing remat (Your Company). letterhead design. When positioned properly, it will serve to work in harmony with all other elements letterhead. This letterhead design is meant to project an image</p>
      <p class="letter__para">This letterhead design is meant project an image of professionalism reliability. By using simple aligen we have created a very spacious feeling. The simplicity suggest rengthtne spaciousnes contributes h aesthetics the layout. These basic qualities along with the (Your Company)</p>
      <p class="letter__para">look and helps reinforce the (Your Company) brand. letterhead design is meant to project an image p design. When positioned properly, it will serve to work in harmony all the other elements letterhead. sionelism and reliability.</p>
      <p class="letter__para">This letterhead design is based on the (Form of your logo) form (Your Company) logo. Each stationery we have created a very spacious feeling. The simplicity suggests strength the spaciousnes contribute part of the (Form of your logo).</p>
      <div class="signature" role="img" aria-label="Handwritten signature"></div>
      <p class="signoff__name">Daniel Ostrow</p>
      <p class="signoff__role">Manager</p>
    </section>

    <footer class="footer-web"><span class="footer-web__prefix">www.</span>brightpathplus.com</footer>

    <div class="band band--bottom-accent"></div>
    <div class="band band--bottom-main"></div>
  </main>
</body>
</html>
```